Alberta, Canada based Environmental Oilfield Consultant need a Business Card Design

We need a business card design for a year old company based in Edmonton, Alberta, Canada called Cindermoor Consulting Inc. We are environmental consultants primarily for oilfield based companies (pipeline cleanup, site consultations, environmental site training, and site evaluations).

We like the color blue or green, something very clean and crisp looking.
We don't really care if there is an otter on it but most of our work is land based and nothing really to do with oceans or larger bodies of water.

The name Cindermoor was the name of our fathers boat, and named our company that in his memory.

```html
<!DOCTYPE html>
<html lang="en">
<head>
<meta charset="utf-8">
<title>Cindermoor Consulting – Business Card</title>
<link href="https://fonts.googleapis.com/css2?family=Exo+2:wght@400;500;600&display=swap" rel="stylesheet">
<style>
  :root {
    --page-bg: #e9ecef;
    --card-white: #ffffff;
    --card-mist: #e8eaec;
    --blue-deep: #1f5fc4;
    --blue-mid: #1a8fe0;
    --blue-light: #12b2f0;
    --teal: #5fb8c4;
    --logo-blue: #2a78c8;
    --text-white: #ffffff;
  }
  * { margin: 0; padding: 0; box-sizing: border-box; }
  html, body {
    width: 1200px; height: 900px; overflow: hidden;
    background: var(--page-bg);
    font-family: "Exo 2", sans-serif;
  }
  .business-card {
    position: absolute;
    left: 100px; top: 165px;
    width: 1000px; height: 570px;
    background: linear-gradient(160deg, var(--card-white) 0%, var(--card-mist) 70%);
    box-shadow: 0 14px 40px rgba(0,0,0,0.18);
    overflow: hidden;
  }
  .card-waves { position: absolute; inset: 0; width: 100%; height: 100%; }
  .company-name {
    position: absolute;
    left: 80px; top: 145px;
    font-weight: 600;
    font-size: 56px;
    line-height: 1.0;
    color: var(--logo-blue);
    letter-spacing: 0.5px;
  }
  .contact-list {
    position: absolute;
    right: 34px; top: 218px;
    list-style: none;
    text-align: right;
    color: var(--text-white);
    font-size: 18px;
    line-height: 1.4;
    letter-spacing: 0.8px;
  }
  .contact-list li { display: flex; justify-content: flex-end; align-items: center; gap: 10px; }
  .contact-list .address { margin-bottom: 12px; }
  .contact-list .address span { display: block; }
  .contact-icon { width: 17px; height: 17px; flex: none; }
  .person {
    position: absolute;
    left: 305px; bottom: 44px;
    color: var(--text-white);
  }
  .person-name { font-size: 24px; font-weight: 500; letter-spacing: 2px; }
  .person-title { font-size: 18px; font-weight: 400; letter-spacing: 0.8px; }
</style>
</head>
<body>
  <article class="business-card">
    <svg class="card-waves" viewBox="0 0 1000 570" preserveAspectRatio="none" aria-hidden="true">
      <defs>
        <radialGradient id="blueGlow" cx="0.68" cy="0.62" r="0.6">
          <stop offset="0" stop-color="var(--blue-light)"/>
          <stop offset="0.55" stop-color="var(--blue-mid)"/>
          <stop offset="1" stop-color="var(--blue-deep)"/>
        </radialGradient>
      </defs>
      <path d="M130 570 C 230 330, 560 170, 1000 100 L1000 570 Z" fill="var(--blue-deep)"/>
      <path d="M150 570 C 250 335, 575 180, 1000 117 L1000 570 Z" fill="var(--card-white)"/>
      <path d="M164 570 C 264 338, 588 187, 1000 127 L1000 570 Z" fill="var(--teal)"/>
      <path d="M182 570 C 282 342, 604 195, 1000 140 L1000 570 Z" fill="var(--card-white)"/>
      <path d="M200 570 C 300 345, 620 200, 1000 150 L1000 570 Z" fill="url(#blueGlow)"/>
    </svg>

    <h1 class="company-name">Cindermoor<br>Consulting</h1>

    <ul class="contact-list">
      <li class="address"><div><span>204, 9th floor Tower</span><span>Whyte Avenue NW AB</span></div></li>
      <li>780 555 0142
        <svg class="contact-icon" viewBox="0 0 24 24"><path fill="#fff" d="M6.6 10.8a15 15 0 0 0 6.6 6.6l2.2-2.2a1 1 0 0 1 1-.25 11.4 11.4 0 0 0 3.6.57 1 1 0 0 1 1 1V20a1 1 0 0 1-1 1A17 17 0 0 1 3 4a1 1 0 0 1 1-1h3.5a1 1 0 0 1 1 1c0 1.25.2 2.45.57 3.57a1 1 0 0 1-.25 1z"/></svg>
      </li>
      <li>780 555 0143
        <svg class="contact-icon" viewBox="0 0 24 24"><rect x="7" y="2" width="10" height="20" rx="2" fill="none" stroke="#fff" stroke-width="2"/><circle cx="12" cy="18" r="1.2" fill="#fff"/></svg>
      </li>
      <li>780 555 0144
        <svg class="contact-icon" viewBox="0 0 24 24"><rect x="3" y="9" width="18" height="10" rx="1.5" fill="#fff"/><rect x="7" y="3" width="10" height="6" fill="none" stroke="#fff" stroke-width="2"/></svg>
      </li>
      <li>info@cindermoor.ca
        <svg class="contact-icon" viewBox="0 0 24 24"><rect x="2" y="5" width="20" height="14" rx="1.5" fill="#fff"/><path d="M2 6l10 7 10-7" fill="none" stroke="var(--blue-mid)" stroke-width="1.8"/></svg>
      </li>
      <li>www.cindermoor.ca
        <svg class="contact-icon" viewBox="0 0 24 24"><circle cx="12" cy="12" r="9.5" fill="none" stroke="#fff" stroke-width="2"/><ellipse cx="12" cy="12" rx="4" ry="9.5" fill="none" stroke="#fff" stroke-width="1.6"/><path d="M2.5 12h19M4 7h16M4 17h16" stroke="#fff" stroke-width="1.4"/></svg>
      </li>
    </ul>

    <div class="person">
      <p class="person-name">JORDAN ELLERY</p>
      <p class="person-title">Managing Director</p>
    </div>
  </article>
</body>
</html>
```